Corvana Tongue Works, LLC

We need a business card that includes information about our business and conveys a reliable business that provides document translation services and interpreters for a variety of corporate and individual clients. We want to come across as professional, reliable, yet approachable. It should include the following on one side:

ESL / ENL Language Classes, Private Lessons, and Online Tutors
PLEXA Training and Testing
Translating & Interpreting Services
Contact us about Over-the-Phone Interpreting in over 200 languages
24/7/365
www.corvanatongue.example

The other side should include (555) 481-3062

Rhoda Pelling, President
482 Garnet Ave., Ste. 219
Indianapolis, IN 40917

Please add USA as part of the address. Also, please add rmpelling@corvanatongueworks.example as the e-mail address. Thank you.

Target Market(s)

Business professionals, their families, the international community

Industry/Entity Type

Business

Contact Information for Business Card

24/7/365
www.corvanatongue.example

(555) 481-3062

Rhoda Pelling, President
482 Garnet Ave., Ste. 219
Indianapolis, IN 40917
USA

Font styles to use
Sans Serif

Colors

Designer to choose colors to be used in the design.

Requirements
Must have
• See project description
• e-mail address and web address
• Phone number
Nice to have
• a globe
• physical address
Should not have
• Should not have the same color scheme as other agencies in our market in Indiana unless it is blue and black. No purple or yellow.

```html
<!DOCTYPE html>
<html lang="en">
<head>
<meta charset="utf-8">
<title>Corvana Tongue Works – Business Cards</title>
<link href="https://fonts.googleapis.com/css2?family=Lato:ital,wght@0,400;0,700;1,700&display=swap" rel="stylesheet">
<style>
  :root {
    --backdrop: #e6e2dc;
    --brand-blue: #2a98d6;
    --ink: #1c1c1c;
    --muted: #444;
    --rule: #8a8a8a;
    --card-white: #f4f4f4;
    --card-ice: #d3f1fc;
    --card-blue: #2196d6;
    --white: #ffffff;
  }
  * { box-sizing: border-box; margin: 0; padding: 0; }
  html, body { width: 1200px; height: 769px; overflow: hidden; }
  body {
    background: var(--backdrop);
    font-family: "Lato", sans-serif;
    color: var(--ink);
    position: relative;
  }
  .card {
    position: absolute;
    width: 480px;
    height: 275px;
    border-radius: 14px;
    overflow: hidden;
    box-shadow: 0 3px 8px rgba(0,0,0,.25);
  }
  .card--front { left: 103px; top: 91px; background: var(--card-white); }
  .card--back-white { left: 618px; top: 91px; background: var(--card-white); }
  .card--back-ice { left: 101px; top: 403px; background: var(--card-ice); }
  .card--back-blue { left: 616px; top: 403px; background: var(--card-blue); color: var(--white); }

  /* front */
  .brand {
    position: absolute; left: 260px; top: 34px;
    display: flex; align-items: center; gap: 8px;
  }
  .brand__dot {
    width: 80px; height: 80px; border-radius: 50%;
    background: var(--brand-blue);
  }
  .brand__name {
    font-size: 21px; line-height: 25px; font-weight: 400; color: var(--ink);
  }
  .holder { position: absolute; left: 23px; top: 171px; }
  .holder__name { font-size: 19px; font-weight: 700; color: var(--brand-blue); letter-spacing: -.2px; }
  .holder__title { font-size: 13.5px; font-weight: 700; margin-top: 1px; }
  .divider {
    position: absolute; left: 23px; right: 31px; top: 214px;
    border-top: 1px solid var(--rule);
  }
  .contact {
    position: absolute; left: 26px; top: 222px;
    font-size: 12px; line-height: 15.5px; color: var(--muted);
  }
  .contact__row { display: flex; align-items: center; gap: 6px; }
  .contact__row svg { width: 10px; height: 10px; fill: var(--brand-blue); }
  .address {
    position: absolute; right: 31px; top: 222px;
    font-size: 12px; line-height: 15.5px; color: var(--muted); text-align: right;
  }

  /* backs */
  .world-map {
    position: absolute; left: 10px; right: 10px; top: 6px; bottom: 10px;
    border-radius: 40px;
    background: radial-gradient(ellipse at center, rgba(0,0,0,.06), rgba(0,0,0,0) 70%);
  }
  .card--back-blue .world-map {
    background: radial-gradient(ellipse at center, rgba(255,255,255,.12), rgba(255,255,255,0) 70%);
  }
  .back-content {
    position: absolute; inset: 0; text-align: center;
  }
  .back-brand {
    position: absolute; left: 0; right: 0; top: 44px;
    display: flex; justify-content: center; align-items: center; gap: 8px;
  }
  .back-brand__dot {
    width: 46px; height: 46px; border-radius: 50%;
    background: var(--brand-blue);
  }
  .card--back-blue .back-brand__dot { background: var(--white); }
  .back-brand__name { font-size: 18px; font-weight: 700; color: var(--brand-blue); }
  .card--back-blue .back-brand__name { color: var(--white); }
  .services {
    position: absolute; left: 0; right: 0; top: 109px;
    font-size: 12.6px; line-height: 15.3px;
  }
  .callout {
    position: absolute; left: 0; right: 0; top: 163px;
    font-size: 14.6px; line-height: 17px; text-transform: uppercase;
  }
  .availability {
    position: absolute; left: 0; right: 0; top: 204px;
    font-size: 17px; font-weight: 700; font-style: italic;
    display: flex; justify-content: center; align-items: center; gap: 5px;
  }
  .availability svg { width: 16px; height: 16px; }
  .website {
    position: absolute; left: 0; right: 0; top: 227px;
    font-size: 14.6px; color: var(--brand-blue);
  }
  .website strong { font-weight: 700; text-transform: uppercase; }
  .card--back-blue .website { color: var(--white); }
</style>
</head>
<body>

  <section class="card card--front" aria-label="Card front">
    <div class="brand">
      <span class="brand__dot"></span>
      <div class="brand__name">Corvana<br>Tongue Works<br>LLC</div>
    </div>
    <div class="holder">
      <div class="holder__name">RHODA PELLING</div>
      <div class="holder__title">PRESIDENT</div>
    </div>
    <div class="divider"></div>
    <div class="contact">
      <div class="contact__row">
        <svg viewBox="0 0 24 24"><path d="M6.6 10.8a15.1 15.1 0 0 0 6.6 6.6l2.2-2.2c.3-.3.7-.4 1-.2 1.1.4 2.3.6 3.6.6.6 0 1 .4 1 1V20c0 .6-.4 1-1 1A17 17 0 0 1 3 4c0-.6.4-1 1-1h3.5c.6 0 1 .4 1 1 0 1.3.2 2.5.6 3.6.1.3 0 .7-.2 1z"/></svg>
        <span>(555) 481-3062</span>
      </div>
      <div class="contact__row">
        <svg viewBox="0 0 24 24"><path d="M2 5h20v14H2z M2 5l10 8 10-8" stroke="#fff" stroke-width="1.5"/></svg>
        <span>rmpelling@corvanatongueworks.example</span>
      </div>
    </div>
    <div class="address">
      482 Garnet Ave., Ste. 219<br>
      Indianapolis, IN 40917
    </div>
  </section>

  <section class="card card--back-white" aria-label="Card back, white version">
    <div class="world-map" role="img" aria-label="Faint dotted world map background"></div>
    <div class="back-content">
      <div class="back-brand"><span class="back-brand__dot"></span><span class="back-brand__name">Corvana</span></div>
      <p class="services">ESL / ENL Language Classes, Private Lessons, &amp; Online Tutors<br>PLEXA Training &amp; Testing<br>Translating &amp; Interpreting Services</p>
      <p class="callout">Contact us about over-the-phone<br>interpreting in over 200 languages</p>
      <p class="availability"><svg viewBox="0 0 16 16" fill="none" stroke="currentColor" stroke-width="1.3"><circle cx="8" cy="8" r="6.8"/><path d="M8 8 L6 12"/></svg>24/7/365</p>
      <p class="website">www.<strong>corvanatongue</strong>.example</p>
    </div>
  </section>

  <section class="card card--back-ice" aria-label="Card back, light blue version">
    <div class="world-map" role="img" aria-label="Faint dotted world map background"></div>
    <div class="back-content">
      <div class="back-brand"><span class="back-brand__dot"></span><span class="back-brand__name">Corvana</span></div>
      <p class="services">ESL / ENL Language Classes, Private Lessons, &amp; Online Tutors<br>PLEXA Training &amp; Testing<br>Translating &amp; Interpreting Services</p>
      <p class="callout">Contact us about over-the-phone<br>interpreting in over 200 languages</p>
      <p class="availability"><svg viewBox="0 0 16 16" fill="none" stroke="currentColor" stroke-width="1.3"><circle cx="8" cy="8" r="6.8"/><path d="M8 8 L6 12"/></svg>24/7/365</p>
      <p class="website">www.<strong>corvanatongue</strong>.example</p>
    </div>
  </section>

  <section class="card card--back-blue" aria-label="Card back, blue version">
    <div class="world-map" role="img" aria-label="Faint dotted world map background"></div>
    <div class="back-content">
      <div class="back-brand"><span class="back-brand__dot"></span><span class="back-brand__name">Corvana</span></div>
      <p class="services">ESL / ENL Language Classes, Private Lessons, &amp; Online Tutors<br>PLEXA Training &amp; Testing<br>Translating &amp; Interpreting Services</p>
      <p class="callout">Contact us about over-the-phone<br>interpreting in over 200 languages</p>
      <p class="availability"><svg viewBox="0 0 16 16" fill="none" stroke="currentColor" stroke-width="1.3"><circle cx="8" cy="8" r="6.8"/><path d="M8 8 L6 12"/></svg>24/7/365</p>
      <p class="website">www.<strong>corvanatongue</strong>.example</p>
    </div>
  </section>

</body>
</html>
```